Christmas Collection Candle Label Design

Looking to update our existing Christmas Candle Collection labels. Labels should reflect the overall feel of our brand- www.kelvanoro.ca
Want to include some color elements. Holiday colors added into design but more muted/ earthy tones not vibrant colors . Metallic elements and line art botanical illustration. Fonts should be more align to brand
Scents
Holiday Tree
Candy Cane
Sugar and Spice
Joyeaux Noel

```html
<!DOCTYPE html>
<html lang="en">
<head>
<meta charset="utf-8">
<title>Sugar &amp; Spice – Christmas Collection Candle Label</title>
<link rel="stylesheet" href="https://fonts.googleapis.com/css2?family=Open+Sans:wght@400;600&display=swap">
<style>
  :root {
    --backdrop: #c3b7b9;
    --label-paper: #f3f3f3;
    --ink: #262626;
    --mauve: #9b5866;
    --art-light: #f1f1f1;
    --art-mid: #dcdcdc;
  }
  * { box-sizing: border-box; margin: 0; padding: 0; }
  html, body {
    width: 1200px;
    height: 748px;
    overflow: hidden;
    background: var(--backdrop);
  }
  .canvas {
    position: relative;
    width: 1200px;
    height: 748px;
  }
  .label {
    position: absolute;
    left: 240px;
    top: 80px;
    width: 720px;
    height: 588px;
    background: var(--label-paper);
    overflow: hidden;
    font-family: "Open Sans", sans-serif;
    color: var(--ink);
  }
  .botanical-art {
    position: absolute;
    left: 16px;
    top: 110px;
    width: 688px;
    height: 220px;
    background: linear-gradient(180deg, var(--art-light) 0%, var(--art-mid) 100%);
  }
  .label-lines {
    position: absolute;
    inset: 0;
    width: 720px;
    height: 588px;
  }
  .tagline {
    position: absolute;
    top: 387px;
    left: 0;
    width: 100%;
    text-align: center;
    font-size: 15px;
    font-weight: 400;
    letter-spacing: 0.3px;
  }
  .scent-name {
    position: absolute;
    top: 440px;
    left: 0;
    width: 100%;
    text-align: center;
    font-size: 58px;
    font-weight: 600;
    letter-spacing: 2px;
    line-height: 1;
  }
  .scent-name .amp { color: var(--mauve); }
  .footer-text {
    font-family: "Open Sans", sans-serif;
    font-size: 13px;
    fill: #ffffff;
    letter-spacing: 0.4px;
  }
</style>
</head>
<body>
<main class="canvas">
  <section class="label">
    <div class="botanical-art" role="img" aria-label="Line art illustration of wildflowers, herbs and leafy stems growing along the band"></div>

    <svg class="label-lines" viewBox="0 0 720 588" aria-hidden="true">
      <!-- ground band -->
      <path d="M16 318 Q360 376 704 314 L704 326 Q360 390 16 330 Z" fill="var(--ink)"/>
      <path d="M16 340 Q360 398 704 336" fill="none" stroke="var(--mauve)" stroke-width="2"/>
      <!-- footer band -->
      <path d="M0 519 Q360 615 720 510 L720 588 L0 588 Z" fill="var(--mauve)"/>
      <path d="M0 519 Q360 615 720 510" fill="none" stroke="var(--ink)" stroke-width="2"/>
      <path id="footer-curve" d="M0 539 Q360 635 720 530" fill="none"/>
      <text class="footer-text">
        <textPath href="#footer-curve" startOffset="50%" text-anchor="middle">13 OZ &#160;&#160;//&#160;&#160; CHRISTMAS COLLECTION &#160;&#160;//&#160;&#160; KELVANORO &#160;&#160;//&#160;&#160; MADE IN CANADA</textPath>
      </text>
    </svg>

    <p class="tagline">MADE WITH PLANT BASED BOTANICAL</p>
    <h1 class="scent-name">SUGAR <span class="amp">&amp;</span> SPICE</h1>
  </section>
</main>
</body>
</html>
```